Trading Company needs a business card design, letter head design and email signature

We need a double-sided business card design, letter head design and an email signature. We have a logo design.

Possible Tag Lines:
• “Connecting Worlds, Building Excellence.”
• “Global Sourcing, Local Excellence.”
• “Bridging Borders, Building Quality.”
• “Worldwide Partnerships, Superior Goods.”
• “Where Quality Meets Affordability”

Services Offered:
Procurement
Fabrication
Distribution
Logistics
Import/Export

Requirements
Must have
• Nice quality double sided Business Card design, Letterhead design needs to be A4
Nice to have
• possible ideas on tag lines

```html
<!DOCTYPE html>
<html lang="en">
<head>
<meta charset="utf-8">
<title>Korvane Business Card</title>
<link rel="stylesheet" href="https://fonts.googleapis.com/css2?family=Open+Sans:wght@400;600;700;800&display=swap">
<style>
  :root {
    --stage: #333333;
    --red: #ec2227;
    --grey: #55585b;
    --ink: #1b1b1b;
    --paper: #ffffff;
    --night: #212125;
    --mist: #e9e9ea;
  }
  * { box-sizing: border-box; margin: 0; padding: 0; }
  html, body { width: 1200px; height: 780px; overflow: hidden; }
  body {
    background: var(--stage);
    font-family: "Open Sans", Arial, sans-serif;
    display: flex;
    align-items: center;
    justify-content: center;
    gap: 24px;
  }
  .card {
    width: 564px;
    height: 322px;
    position: relative;
    overflow: hidden;
    box-shadow: 0 14px 30px rgba(0,0,0,.45);
  }

  /* Front */
  .card--front { background: var(--paper); }
  .front-brand {
    position: absolute; left: 44px; top: 40px;
    display: flex; align-items: center; gap: 10px;
  }
  .brand-square { width: 22px; height: 22px; background: var(--red); }
  .brand-name {
    font-weight: 800; font-size: 36px; letter-spacing: 3px;
    color: var(--red); line-height: 1;
  }
  .identity { position: absolute; left: 44px; top: 118px; }
  .identity-name {
    font-weight: 800; font-size: 30px; line-height: 1.05; color: var(--red);
  }
  .identity-name .surname { color: var(--grey); }
  .identity-role { font-size: 15px; font-weight: 600; color: var(--ink); margin-top: 4px; }
  .divider {
    position: absolute; left: 318px; top: 46px; width: 1.5px; height: 120px;
    background: var(--red);
  }
  .contacts {
    position: absolute; left: 338px; top: 58px;
    list-style: none; display: flex; flex-direction: column; gap: 10px;
  }
  .contacts li {
    display: flex; align-items: center; gap: 9px;
    font-size: 14px; color: var(--ink);
  }
  .contact-icon { width: 18px; height: 18px; flex: none; }
  .services-label {
    position: absolute; left: 44px; top: 222px;
    font-weight: 700; font-size: 14px; color: var(--red); letter-spacing: .5px;
  }
  .services-band {
    position: absolute; left: 0; right: 0; bottom: 22px; height: 40px;
    background: var(--red);
    display: flex; align-items: center; justify-content: center; gap: 12px;
    list-style: none;
  }
  .services-band li {
    display: flex; align-items: center; gap: 7px;
    color: var(--paper); font-size: 14px; font-weight: 600;
  }
  .services-band li::before {
    content: ""; width: 7px; height: 7px; background: var(--paper);
  }

  /* Back */
  .card--back { background: var(--night); }
  .back-brand {
    position: absolute; left: 0; right: 0; top: 84px;
    display: flex; align-items: center; justify-content: center; gap: 14px;
  }
  .back-brand .brand-square { width: 34px; height: 34px; }
  .back-brand .brand-name { font-size: 60px; letter-spacing: 5px; }
  .taglines {
    position: absolute; left: 0; right: 0; top: 196px;
    list-style: none; display: flex; flex-wrap: wrap; justify-content: center;
    gap: 8px 16px; padding: 0 34px;
  }
  .taglines li {
    display: flex; align-items: center; gap: 7px;
    color: var(--mist); font-size: 13px; letter-spacing: .3px;
  }
  .taglines li::before {
    content: ""; width: 8px; height: 8px; background: var(--red);
  }
</style>
</head>
<body>

  <section class="card card--front" aria-label="Business card front">
    <div class="front-brand">
      <span class="brand-square"></span>
      <span class="brand-name">KORVANE</span>
    </div>

    <div class="identity">
      <p class="identity-name">Lukas <span class="surname">Verhoven</span></p>
      <p class="identity-role">Managing Director</p>
    </div>

    <span class="divider"></span>

    <ul class="contacts">
      <li>
        <svg class="contact-icon" viewBox="0 0 24 24" aria-hidden="true"><circle cx="12" cy="12" r="12" fill="#ec2227"/><path d="M8.2 6.5l2 .1.9 2.6-1.3 1c.7 1.5 1.8 2.6 3.2 3.3l1-1.3 2.6.9.1 2c-.1.8-.8 1.3-1.6 1.2C10.6 15.9 8 13.3 7.5 8.1c-.1-.8.4-1.5 1.2-1.6z" fill="#fff"/></svg>
        (555) 014-2290
      </li>
      <li>
        <svg class="contact-icon" viewBox="0 0 24 24" aria-hidden="true"><circle cx="12" cy="12" r="12" fill="#ec2227"/><rect x="6" y="8" width="12" height="8.5" rx="1" fill="#fff"/><path d="M6.5 8.5l5.5 4.2 5.5-4.2" fill="none" stroke="#ec2227" stroke-width="1.2"/></svg>
        info@korvane.com
      </li>
      <li>
        <svg class="contact-icon" viewBox="0 0 24 24" aria-hidden="true"><circle cx="12" cy="12" r="12" fill="#ec2227"/><g fill="none" stroke="#fff" stroke-width="1.2"><circle cx="12" cy="12" r="6"/><ellipse cx="12" cy="12" rx="2.6" ry="6"/><path d="M6 12h12M7 9h10M7 15h10"/></g></svg>
        www.korvane.com
      </li>
    </ul>

    <p class="services-label">SERVICES</p>
    <ul class="services-band">
      <li>Procurement</li>
      <li>Fabrication</li>
      <li>Distribution</li>
      <li>Logistics</li>
      <li>Import/Export</li>
    </ul>
  </section>

  <section class="card card--back" aria-label="Business card back">
    <div class="back-brand">
      <span class="brand-square"></span>
      <span class="brand-name">KORVANE</span>
    </div>
    <ul class="taglines">
      <li>Connecting Worlds, Building Excellence</li>
      <li>Global Sourcing, Local Excellence</li>
      <li>Bridging Borders, Building Quality</li>
      <li>Worldwide Partnerships, Superior Goods</li>
      <li>Where Quality Meets Affordability</li>
    </ul>
  </section>

</body>
</html>
```